Business Card Design using new attached logo

We are a family run Plumbing and Heating firm looking to improve our company image with an improved business card and new logo.We are looking to keep the company colour (Blue) involved in our design

Reason: New logo added which needs to be incorporated on designs

Industry/Entity Type

Business

Contact Information for Business Card

See attachment of all info required.

Requirements
Must have
• We have just picked a new company logo which is attached.
• Could you please provide your business card designs using this logo.
• We are looking for the logo on the back as well as the front with all the info required

```html
<!DOCTYPE html>
<html lang="en">
<head>
<meta charset="utf-8">
<title>HKM Services – Business Card</title>
<link rel="stylesheet" href="https://fonts.googleapis.com/css2?family=Marcellus+SC&family=Source+Sans+3:ital,wght@0,400;0,600;1,400&display=swap">
<style>
  :root {
    --stage: #333333;
    --card-white: #ffffff;
    --blue-light: #3a86c9;
    --blue-mid: #2a5ea3;
    --blue-deep: #1e3b7a;
    --navy-text: #243a78;
    --white-text: #ffffff;
    --shadow: rgba(0, 0, 0, 0.45);
  }
  html, body {
    margin: 0;
    padding: 0;
    width: 1200px;
    height: 907px;
    overflow: hidden;
    background: var(--stage);
  }
  .stage {
    position: relative;
    width: 1200px;
    height: 907px;
  }
  .card {
    position: absolute;
    left: 300px;
    width: 600px;
    height: 343px;
    box-shadow: 0 3px 8px var(--shadow);
    overflow: hidden;
  }
  .card--front {
    top: 92px;
    background: radial-gradient(ellipse 330px 260px at 301px 154px, var(--blue-light) 0%, var(--blue-mid) 55%, var(--blue-deep) 100%);
    color: var(--white-text);
  }
  .card--back {
    top: 472px;
    background: var(--card-white);
  }
  .holder-name {
    position: absolute;
    left: 39px;
    top: 30px;
    margin: 0;
    font-family: "Marcellus SC", serif;
    font-size: 24px;
    font-weight: 400;
    letter-spacing: 0.5px;
  }
  .holder-role {
    position: absolute;
    left: 39px;
    top: 62px;
    margin: 0;
    font-family: "Marcellus SC", serif;
    font-size: 19px;
    font-weight: 400;
    letter-spacing: 0.4px;
  }
  .address {
    position: absolute;
    left: 39px;
    top: 99px;
    margin: 0;
    font-family: "Source Sans 3", sans-serif;
    font-style: normal;
    font-size: 16px;
    line-height: 20.5px;
  }
  .contacts {
    position: absolute;
    left: 39px;
    top: 189px;
    margin: 0;
    padding: 0;
    list-style: none;
    font-family: "Source Sans 3", sans-serif;
    font-size: 16px;
    line-height: 24px;
  }
  .contacts li {
    display: flex;
    align-items: center;
    height: 24px;
  }
  .contacts svg {
    width: 15px;
    height: 15px;
    margin-right: 10px;
    fill: var(--white-text);
    flex: none;
  }
  .brand {
    position: absolute;
    display: flex;
    align-items: center;
    gap: 10px;
    font-family: "Source Sans 3", sans-serif;
    font-weight: 600;
    white-space: nowrap;
  }
  .brand__dot {
    border-radius: 50%;
    flex: none;
  }
  .brand--front {
    right: 44px;
    top: 243px;
    font-size: 32px;
    color: var(--white-text);
  }
  .brand--front .brand__dot {
    width: 18px;
    height: 18px;
    background: var(--white-text);
  }
  .brand--back {
    left: 0;
    right: 0;
    top: 146px;
    justify-content: center;
    font-size: 40px;
    color: var(--blue-mid);
  }
  .brand--back .brand__dot {
    width: 22px;
    height: 22px;
    background: var(--blue-mid);
  }
  .tagline {
    position: absolute;
    left: 0;
    right: 0;
    top: 282px;
    margin: 0;
    text-align: center;
    font-family: "Source Sans 3", sans-serif;
    font-style: italic;
    font-size: 16.5px;
    color: var(--navy-text);
    letter-spacing: 0.2px;
  }
</style>
</head>
<body>
<main class="stage">
  <section class="card card--front" aria-label="Business card front">
    <h1 class="holder-name">Daniel Hartley</h1>
    <p class="holder-role">Director</p>
    <address class="address">
      HKM Services Ltd<br>
      14 Mill Terrace<br>
      Ashford Road<br>
      Redhill, RH14QP
    </address>
    <ul class="contacts">
      <li>
        <svg viewBox="0 0 16 16" aria-hidden="true"><path d="M3.5 1.5c.6-.4 1.3-.2 1.6.4l1.2 2.3c.3.6.1 1.2-.4 1.5l-1 .6c.7 1.8 2 3.3 3.8 4.3l.7-.9c.4-.5 1.1-.6 1.6-.2l2.1 1.5c.5.4.6 1.1.2 1.6l-.9 1.2c-.5.6-1.3.8-2 .5C6 12.6 2.9 9.2 1.9 4.8c-.2-.8.1-1.6.7-2.1z"/></svg>
        020 7946 0321
      </li>
      <li>
        <svg viewBox="0 0 16 16" aria-hidden="true"><path d="M4 1h7l1 1v3H4zM2 6h12a1 1 0 0 1 1 1v5H1V7a1 1 0 0 1 1-1zm2 7h8v2H4z"/></svg>
        020 7946 0488
      </li>
      <li>
        <svg viewBox="0 0 16 16" aria-hidden="true"><path d="M5 0h1v2h4a1 1 0 0 1 1 1v12a1 1 0 0 1-1 1H5a1 1 0 0 1-1-1V3a1 1 0 0 1 1-1zm1 4v4h4V4zm0 6v1h1v-1zm2 0v1h1v-1zm-2 2v1h1v-1zm2 0v1h1v-1z"/></svg>
        07700900612
      </li>
      <li>
        <svg viewBox="0 0 16 16" aria-hidden="true"><path d="M1 4h14v9H1zm1.5 1L8 9l5.5-4z" fill-rule="evenodd"/></svg>
        danielhartley@hkmservicesltd.co.uk
      </li>
      <li>
        <svg viewBox="0 0 16 16" aria-hidden="true"><path d="M8 1a7 7 0 1 0 0 14A7 7 0 0 0 8 1zm0 1.3c.8.8 1.4 2.1 1.6 3.7H6.4C6.6 4.4 7.2 3.1 8 2.3zM5.1 6H2.6a5.7 5.7 0 0 1 3.5-3.4C5.6 3.5 5.2 4.7 5.1 6zm0 1.3c0 .9.1 1.7.3 2.4H2.5a5.6 5.6 0 0 1 0-2.4zm1.3 0h3.2c0 .9-.1 1.7-.3 2.4H6.7c-.2-.7-.3-1.5-.3-2.4zm4.5 0h2.6a5.6 5.6 0 0 1 0 2.4h-2.9c.2-.7.3-1.5.3-2.4zm2.5-1.3h-2.5c-.1-1.3-.5-2.5-1-3.4A5.7 5.7 0 0 1 13.4 6zM2.9 11h2.8c.2.9.6 1.7 1 2.4A5.7 5.7 0 0 1 2.9 11zm4.1 0h2c-.3.9-.6 1.6-1 2.2-.4-.6-.7-1.3-1-2.2zm3.3 0h2.8a5.7 5.7 0 0 1-3.8 2.4c.4-.7.8-1.5 1-2.4z"/></svg>
        www.hkmservicesltd.co.uk
      </li>
    </ul>
    <div class="brand brand--front">
      <span class="brand__dot" aria-hidden="true"></span>
      <span class="brand__name">HKM Services</span>
    </div>
  </section>

  <section class="card card--back" aria-label="Business card back">
    <div class="brand brand--back">
      <span class="brand__dot" aria-hidden="true"></span>
      <span class="brand__name">HKM Services</span>
    </div>
    <p class="tagline">Plumbing and Heating Services</p>
  </section>
</main>
</body>
</html>
```